Membership Drive "CHRISTMAS SPECIAL"

Looking to run a "Christmas Special" on 6 month Memberships for December 2019 to boost membership number up. This is a great time to get people exercising and everyone loves a Christmas Sale. Special is designed to attract more people to join and enjoy the savings.
Artwork will be display via social media (FP and Pictora) as well as in store. Artwork must be eye catching and direct to the customer. Customer should feel a sense of relief with being able to exercise at a lower cost .

Heading: "Christmas Sale"
6 Months
$199.00 Save over 30%
Terms and conditions apply"
*Offer End 31st December

below are other promos we had designed on Sketch Harbor along with potential photos to be included into this promo

Target Market(s)

Males and Females aged between 16 - 45

Industry/Entity Type

Fitness

Colors

Designer to choose colors to be used in the design.

Requirements
Must have
• Must emphasize "Christmas Special" $199.00 Save over 30%
• Terms and conditions apply
• Offer Ends 31st of December
• "All of our contact details"
• Address: 14 Marlow Rd Fernhill 3187
• Ph: 9428 7160
• www.stridelane.com.au
• Design format must come in PDF for a AO poster and an Pictora format please
Nice to have
• Some Christmas feels to the artwork

```html
<!DOCTYPE html>
<html lang="en">
<head>
<meta charset="utf-8">
<title>Stride Lane Gymnasium – Super Christmas Special</title>
<link href="https://fonts.googleapis.com/css2?family=Great+Vibes&family=Jost:wght@300;400;500;600;700&display=swap" rel="stylesheet">
<style>
  :root {
    --poster-red: #e2364b;
    --panel-deep: #3a0003;
    --panel-mid: #8e0b10;
    --panel-bright: #b3161c;
    --pine-dark: #23744a;
    --pine-light: #74c24c;
    --festive-red: #ec1820;
    --festive-dark: #3b0608;
    --ink: #0d0d0d;
    --white: #ffffff;
    --note: #ecc4c6;
  }
  html, body {
    margin: 0;
    padding: 0;
    width: 849px;
    height: 1200px;
    overflow: hidden;
    background: var(--poster-red);
  }
  .poster {
    display: block;
    width: 849px;
    height: 1200px;
  }
  .brand-name { font-family: "Jost", sans-serif; font-weight: 700; fill: var(--ink); }
  .headline-script { font-family: "Great Vibes", cursive; fill: var(--white); }
  .headline-main {
    font-family: "Jost", sans-serif; font-weight: 600;
    stroke: var(--white); stroke-width: 6; paint-order: stroke; stroke-linejoin: round;
  }
  .headline-sub { font-family: "Jost", sans-serif; font-weight: 300; fill: var(--white); }
  .discount { font-family: "Jost", sans-serif; font-weight: 700; fill: var(--ink); }
  .offer-end { font-family: "Jost", sans-serif; font-weight: 400; fill: var(--note); }
  .price { font-family: "Jost", sans-serif; font-weight: 700; fill: var(--white); }
  .saving { font-family: "Jost", sans-serif; font-weight: 500; fill: var(--white); }
  .contact { font-family: "Jost", sans-serif; font-weight: 500; fill: var(--white); font-variant: small-caps; }
  .terms { font-family: "Jost", sans-serif; font-weight: 400; fill: var(--white); font-variant: small-caps; }
</style>
</head>
<body>
<svg class="poster" viewBox="0 0 849 1200" xmlns="http://www.w3.org/2000/svg">
  <defs>
    <linearGradient id="pineTone" x1="0" y1="0" x2="1" y2="1">
      <stop offset="0" stop-color="var(--pine-light)"/>
      <stop offset="0.5" stop-color="var(--pine-dark)"/>
      <stop offset="1" stop-color="var(--pine-light)"/>
    </linearGradient>
    <linearGradient id="photoTone" x1="0" y1="0" x2="1" y2="1">
      <stop offset="0" stop-color="var(--panel-bright)"/>
      <stop offset="0.55" stop-color="var(--panel-mid)"/>
      <stop offset="1" stop-color="var(--panel-deep)"/>
    </linearGradient>
    <linearGradient id="headlineFill" x1="0" y1="0" x2="1" y2="0">
      <stop offset="0" stop-color="var(--festive-dark)"/>
      <stop offset="0.5" stop-color="var(--festive-red)"/>
      <stop offset="1" stop-color="var(--festive-dark)"/>
    </linearGradient>
    <filter id="softEdge" x="-5%" y="-5%" width="110%" height="110%">
      <feGaussianBlur stdDeviation="6"/>
    </filter>
    <filter id="panelShadow" x="-5%" y="-5%" width="110%" height="110%">
      <feDropShadow dx="0" dy="2" stdDeviation="3" flood-color="#000" flood-opacity="0.35"/>
    </filter>
  </defs>

  <rect class="poster-ground" width="849" height="1200" fill="var(--poster-red)"/>

  <g class="pine-garland" role="img" aria-label="Pine branch garland framing the poster">
    <path filter="url(#softEdge)" fill="url(#pineTone)" fill-rule="evenodd"
      d="M-20 -20 H869 V1220 H-20 Z M70 80 Q60 60 110 62 H740 Q790 60 782 100 V1090 Q790 1118 740 1112 H110 Q62 1118 68 1090 Z"/>
  </g>

  <g class="brand">
    <text class="brand-name" x="424.5" y="126" text-anchor="middle" font-size="34" letter-spacing="1">STRIDE LANE</text>
    <text class="brand-name" x="424.5" y="145" text-anchor="middle" font-size="12" letter-spacing="8.5">GYMNASIUM</text>
  </g>

  <rect class="hero-photo" x="121" y="176" width="607" height="811" fill="url(#photoTone)" filter="url(#panelShadow)"
    role="img" aria-label="Athlete lifting dumbbells, red-toned gym photograph"/>

  <g class="headline">
    <text class="headline-script" x="424" y="444" text-anchor="middle" font-size="128">Super</text>
    <text class="headline-main" x="77" y="552" font-size="130" textLength="694" lengthAdjust="spacingAndGlyphs" fill="url(#headlineFill)">CHRISTMAS</text>
    <text class="headline-sub" x="264" y="625" font-size="92" textLength="317" lengthAdjust="spacingAndGlyphs">SPECIAL</text>
  </g>

  <g class="discount-band">
    <polygon points="199,675 650,675 625,762 175,762" fill="var(--white)"/>
    <text class="discount" x="248" y="747" font-size="80" textLength="361" lengthAdjust="spacingAndGlyphs">30%OFF*</text>
  </g>
  <text class="offer-end" x="618" y="783" text-anchor="end" font-size="12">Offer Ends 31st of December</text>

  <g class="price-block">
    <text class="price" x="285" y="878" font-size="74" textLength="280" lengthAdjust="spacingAndGlyphs">$199.00</text>
    <text class="saving" x="289" y="920" font-size="36" textLength="272" lengthAdjust="spacingAndGlyphs">SAVE OVER 30%</text>
    <text class="saving" x="286" y="941" font-size="18" textLength="279" lengthAdjust="spacingAndGlyphs">WITH 6 MONTHS SUBSCRIPTION</text>
  </g>

  <g class="contact-details">
    <text class="contact" x="424.5" y="1030" text-anchor="middle" font-size="13">Address: 14 Marlow Rd Fernhill 3187</text>
    <text class="contact" x="424.5" y="1049" text-anchor="middle" font-size="13">Ph: 9428 7160</text>
    <text class="contact" x="424.5" y="1068" text-anchor="middle" font-size="11">WWW.STRIDELANE.COM.AU</text>
  </g>

  <text class="terms" x="810" y="1160" text-anchor="end" font-size="11">*Terms and conditions apply</text>
</svg>
</body>
</html>
```